Software as a Service to manage Home Care Management

We need a web site designed for Home Care Management Software as a Service product, that facilitates Home Care organizations to manage and schedule carers to visit client homes. We want a modern look and feel using our existing logo.

Target Market(s)

Home Care Management organizations. Product is similar to: https://carelarkly.io/

Coding

Coded - Design and coding required

Number of Pages Required

3 page

```html
<!DOCTYPE html>
<html lang="en">
<head>
<meta charset="utf-8">
<title>Shiftly Care – Home Care Software</title>
<link href="https://fonts.googleapis.com/css2?family=Cinzel:wght@400;600&family=Open+Sans:wght@400;600;700&display=swap" rel="stylesheet">
<style>
:root{
  --pink:#ec2f7b;
  --pink-soft:#f7a9c8;
  --navy:#0d1f3a;
  --navy-2:#1d3f66;
  --ink:#333;
  --muted:#777;
  --grey-bg:#f1f1f1;
  --black:#0b0b0b;
  --white:#fff;
}
*{box-sizing:border-box;margin:0;padding:0}
html,body{width:1200px;height:3424px;overflow:hidden}
body{font-family:"Open Sans",Arial,sans-serif;color:var(--ink);background:var(--white);position:relative}
.btn{display:inline-block;background:var(--pink);color:var(--white);font-weight:700;font-size:15px;letter-spacing:.5px;padding:12px 30px;border-radius:30px;text-decoration:none}

/* header */
.site-header{position:absolute;top:0;left:0;width:1200px;height:100px;display:flex;align-items:center;padding:0 100px 0 40px}
.brand{display:flex;align-items:center;gap:12px;font-family:"Cinzel",Georgia,serif;font-weight:600;font-size:32px;color:var(--navy);white-space:nowrap}
.brand-dot{width:30px;height:30px;border-radius:50%;background:var(--pink)}
.main-nav{margin-left:auto;display:flex;gap:34px;font-size:15px;font-weight:600;color:var(--navy);white-space:nowrap}
.main-nav .active{color:var(--pink)}
.site-header .btn{margin-left:60px;font-size:14px;padding:12px 26px;white-space:nowrap}

/* hero */
.hero{position:absolute;top:100px;left:0;width:1200px;height:680px;overflow:hidden}
.hero-bg{position:absolute;inset:0;background:radial-gradient(ellipse at 50% 40%,#2c5f8f 0%,#163256 40%,#0a1a30 80%)}
.hero-inner{position:relative;text-align:center;color:var(--white);padding-top:140px}
.hero-mark{width:56px;height:56px;border-radius:50%;background:var(--white);margin:0 auto 14px}
.hero h1{font-family:"Cinzel",Georgia,serif;font-weight:400;font-size:84px;line-height:1}
.hero p{width:560px;margin:26px auto 50px;font-size:15px;line-height:1.6}
.dots{position:absolute;top:520px;left:0;width:100%;display:flex;justify-content:center;gap:10px}
.dots span{width:14px;height:14px;border:2px solid var(--white);border-radius:50%}
.dots span.on{background:var(--white)}
.hero-wave{position:absolute;bottom:0;left:0}

/* optimised */
.feature{position:absolute;top:800px;left:0;width:1200px;height:560px}
.feature-art{position:absolute;left:110px;top:70px;width:400px;height:420px;border-radius:24px;background:radial-gradient(circle at 50% 55%,#f7d6e4 0%,#f2a3c4 55%,#ec2f7b 100%)}
.feature-text{position:absolute;left:600px;top:80px;width:500px}
.feature-text h2{font-family:"Cinzel",Georgia,serif;font-weight:400;font-size:38px;line-height:1.1;color:var(--navy)}
.feature-text p{font-size:13px;line-height:1.7;color:var(--muted);margin-top:18px}
.feature-text .btn{margin-top:30px;font-size:13px;padding:11px 26px}

/* made for */
.audience{position:absolute;top:1380px;left:0;width:1200px;height:520px;background:var(--grey-bg);text-align:center}
.section-title{font-family:"Cinzel",Georgia,serif;font-weight:400;font-size:38px;color:var(--navy)}
.audience .section-title{margin-top:96px}
.audience-list{display:flex;justify-content:center;gap:30px;margin-top:64px}
.audience-item{width:260px}
.ring{width:130px;height:130px;margin:0 auto;display:block}
.audience-item h3{font-size:19px;font-weight:700;color:var(--navy);margin-top:24px;white-space:nowrap}
.audience-item p{font-size:12px;line-height:1.6;color:var(--muted);margin:8px auto 0;width:220px}

/* numbers */
.numbers{position:absolute;top:1900px;left:0;width:1200px;height:620px;text-align:center}
.numbers .section-title{margin-top:80px}
.stats-grid{position:absolute;left:112px;top:180px;width:976px;height:390px;display:grid;grid-template-columns:repeat(3,1fr);grid-template-rows:1fr 1fr}
.photo-a{background:linear-gradient(135deg,#c9b39a,#7d8fa0)}
.photo-b{background:linear-gradient(135deg,#a8c0a0,#d9c7b8)}
.photo-c{background:linear-gradient(135deg,#8fae7a,#d7c1a6)}
.stat{background:var(--pink);color:var(--white);display:flex;flex-direction:column;align-items:center;justify-content:center;padding:0 50px}
.stat strong{font-size:44px;font-weight:600}
.stat span{font-size:12px;line-height:1.5;margin-top:6px}

/* partners */
.partners{position:absolute;top:2540px;left:0;width:1200px;height:470px;background:linear-gradient(180deg,#f7d2e2 0%,#ec2f7b 40%,#8a1146 80%,#c2175f 100%);text-align:center}
.partners .section-title{margin-top:62px;color:var(--navy);font-size:40px}
.partner-row{display:flex;justify-content:center;gap:28px;margin-top:90px;align-items:center}
.partner{width:176px;height:92px;background:var(--white);border-radius:10px;display:flex;align-items:center;justify-content:center}
.partner i{display:block;width:110px;height:34px;border-radius:6px;background:#2a2a2a}
.arrow{position:absolute;top:300px}

/* footer */
.site-footer{position:absolute;top:3010px;left:0;width:1200px;height:414px;background:var(--black);color:var(--white)}
.site-footer h4{font-size:15px;font-weight:700;letter-spacing:.5px}
.contact-form{position:absolute;left:110px;top:46px;width:480px}
.form-grid{display:grid;grid-template-columns:1fr 1fr;gap:12px;margin-top:24px}
.field{background:var(--white);color:#999;font-size:11px;height:30px;padding:8px 10px}
.field.wide{grid-column:1/3;height:70px}
.contact-form .btn{margin-top:16px;font-size:12px;padding:10px 26px}
.quick-links{position:absolute;left:650px;top:46px}
.quick-links ul{list-style:none;margin-top:24px}
.quick-links li{font-size:13px;margin-bottom:10px;padding-left:16px;position:relative}
.quick-links li::before{content:"›";position:absolute;left:0;color:var(--pink);font-weight:700}
.stay{position:absolute;left:650px;top:294px;display:flex;align-items:center;gap:10px;font-size:15px;font-weight:700}
.stay i{width:28px;height:28px;border-radius:50%;display:block;background:var(--pink)}
.contact-us{position:absolute;left:850px;top:46px;width:260px}
.contact-us ul{list-style:none;margin-top:24px}
.contact-us li{font-size:13px;line-height:1.5;margin-bottom:10px;display:flex;gap:10px}
.contact-us svg{flex:none;margin-top:3px}
.copyright{position:absolute;left:110px;right:110px;bottom:0;height:60px;border-top:1px solid #333;text-align:center;font-size:12px;line-height:60px;color:#ccc}
</style>
</head>
<body>

<header class="site-header">
  <div class="brand"><span class="brand-dot"></span>Shiftly Care</div>
  <nav class="main-nav">
    <span class="active">HOME</span><span>PRODUCT</span><span>PRICING</span><span>BLOG</span><span>FAQ</span><span>CONTACT US</span>
  </nav>
  <a class="btn" href="#">BOOK A DEMO</a>
</header>

<section class="hero">
  <div class="hero-bg" role="img" aria-label="Dark blue technology background with glowing data lines"></div>
  <div class="hero-inner">
    <div class="hero-mark"></div>
    <h1>Shiftly Care</h1>
    <p>Plan visits, match carers to clients and keep every family informed from one simple, secure dashboard built for home care teams.</p>
    <a class="btn" href="#">GET STARTED</a>
  </div>
  <div class="dots"><span class="on"></span><span></span><span></span></div>
  <svg class="hero-wave" width="1200" height="140" viewBox="0 0 1200 140">
    <path d="M0 40 Q600 140 1200 40 L1200 140 L0 140Z" fill="#ec2f7b"/>
    <path d="M0 70 Q600 170 1200 70 L1200 140 L0 140Z" fill="#fff"/>
    <path d="M585 70 L600 84 L615 70 M585 82 L600 96 L615 82" stroke="#0d1f3a" stroke-width="3" fill="none"/>
  </svg>
</section>

<section class="feature">
  <div class="feature-art" role="img" aria-label="Illustration of a smartphone showing the carer app, set over a pink ring"></div>
  <div class="feature-text">
    <h2>Optimised Home Care<br>Software</h2>
    <p>Build rosters in minutes with smart scheduling that weighs carer skills, travel time and client preferences. Changes sync instantly to every carer's phone, so visits are never missed and office staff spend less time on calls and more time supporting the people in their care.</p>
    <p>Track visit times, care notes and medication records in real time. Managers see gaps before they happen, while families get clear updates they can trust each day.</p>
    <p>Payroll and invoicing flow straight from completed visits, with no extra data entry needed.</p>
    <a class="btn" href="#">LEARN MORE ›</a>
  </div>
</section>

<section class="audience">
  <h2 class="section-title">We have made Shiftly Care</h2>
  <div class="audience-list">
    <div class="audience-item">
      <svg class="ring" viewBox="0 0 130 130"><circle cx="65" cy="65" r="60" fill="#fff" stroke="#ddd" stroke-width="3"/><path d="M65 5 A60 60 0 0 1 125 65" stroke="#ec2f7b" stroke-width="4" fill="none"/><rect x="47" y="40" width="36" height="48" rx="3" fill="#ec2f7b"/><rect x="57" y="35" width="16" height="9" rx="2" fill="#0d1f3a"/><path d="M54 56h22M54 65h22M54 74h14" stroke="#fff" stroke-width="3"/></svg>
      <h3>For Managers</h3>
      <p>See every shift, gap and visit across your whole team at once.</p>
    </div>
    <div class="audience-item">
      <svg class="ring" viewBox="0 0 130 130"><circle cx="65" cy="65" r="60" fill="#fff" stroke="#ddd" stroke-width="3"/><path d="M65 5 A60 60 0 0 1 125 65" stroke="#ec2f7b" stroke-width="4" fill="none"/><path d="M65 92 L40 66 A14 14 0 0 1 65 48 A14 14 0 0 1 90 66Z" fill="#ec2f7b"/><path d="M38 68h14l5-10 7 18 5-10h23" stroke="#fff" stroke-width="3" fill="none"/></svg>
      <h3>For Carers</h3>
      <p>Daily routes, client notes and check-ins right on your phone.</p>
    </div>
    <div class="audience-item">
      <svg class="ring" viewBox="0 0 130 130"><circle cx="65" cy="65" r="60" fill="#fff" stroke="#ddd" stroke-width="3"/><path d="M65 5 A60 60 0 0 1 125 65" stroke="#ec2f7b" stroke-width="4" fill="none"/><path d="M36 66 L65 40 L94 66 H86 V92 H44 V66Z" fill="#ec2f7b"/><rect x="58" y="72" width="14" height="20" fill="#fff"/></svg>
      <h3>For Clients and Families</h3>
      <p>Clear visit updates and peace of mind for loved ones.</p>
    </div>
  </div>
</section>

<section class="numbers">
  <h2 class="section-title">Success in numbers</h2>
  <div class="stats-grid">
    <div class="photo-a" role="img" aria-label="Photo of a carer sitting with an elderly woman"></div>
    <div class="stat"><strong>96%</strong><span>of visits are delivered on time by teams using our scheduling tools</span></div>
    <div class="photo-c" role="img" aria-label="Photo of an elderly couple smiling outdoors"></div>
    <div class="stat"><strong>13M</strong><span>care visits planned and recorded through the platform so far</span></div>
    <div class="photo-b" role="img" aria-label="Photo of a nurse helping an elderly woman in a garden"></div>
    <div class="stat"><strong>17K</strong><span>carers use the mobile app every week across all providers</span></div>
  </div>
</section>

<section class="partners">
  <h2 class="section-title">Working in association with</h2>
  <svg class="arrow" style="left:28px" width="20" height="30" viewBox="0 0 20 30"><path d="M16 3 L4 15 L16 27" stroke="#fff" stroke-width="4" fill="none"/></svg>
  <svg class="arrow" style="right:28px" width="20" height="30" viewBox="0 0 20 30"><path d="M4 3 L16 15 L4 27" stroke="#fff" stroke-width="4" fill="none"/></svg>
  <div class="partner-row">
    <div class="partner"><i></i></div><div class="partner"><i></i></div><div class="partner"><i></i></div><div class="partner"><i></i></div><div class="partner"><i></i></div>
  </div>
</section>

<footer class="site-footer">
  <div class="contact-form">
    <h4>GET IN TOUCH</h4>
    <div class="form-grid">
      <div class="field">First Name</div><div class="field">Last Name</div>
      <div class="field">Email</div><div class="field">Phone Number</div>
      <div class="field wide">Message</div>
    </div>
    <a class="btn" href="#">SUBMIT</a>
  </div>
  <div class="quick-links">
    <h4>QUICK LINKS</h4>
    <ul><li>Home</li><li>About Us</li><li>Services</li><li>Partners</li><li>Contact Us</li></ul>
  </div>
  <div class="stay">STAY CONNECTED : <i></i><i></i></div>
  <div class="contact-us">
    <h4>CONTACT US</h4>
    <ul>
      <li><svg width="12" height="16" viewBox="0 0 12 16"><path d="M6 0a6 6 0 0 1 6 6c0 4-6 10-6 10S0 10 0 6a6 6 0 0 1 6-6z" fill="#ec2f7b"/><circle cx="6" cy="6" r="2" fill="#000"/></svg>278 Harbour View Road,<br>Westfield, MA 01085</li>
      <li><svg width="14" height="14" viewBox="0 0 14 14"><path d="M3 0l3 3-2 2a8 8 0 0 0 5 5l2-2 3 3-2 3C5 14 0 9 0 3z" fill="#ec2f7b"/></svg>(480) 555-0147</li>
      <li><svg width="14" height="14" viewBox="0 0 14 14"><path d="M3 0l3 3-2 2a8 8 0 0 0 5 5l2-2 3 3-2 3C5 14 0 9 0 3z" fill="#ec2f7b"/></svg>123 456 7890</li>
      <li><svg width="14" height="12" viewBox="0 0 14 12"><rect width="14" height="12" rx="1" fill="#ec2f7b"/><path d="M0 1l7 6 7-6" stroke="#000" fill="none"/></svg>hello@shiftlycare.com</li>
    </ul>
  </div>
  <div class="copyright">© 2020 Shiftly Care | All Rights Reserved | Terms and Conditions</div>
</footer>

</body>
</html>
```